Novexa company website, a website for employment for people with autism

The website will make a match between people and jobs, mainly in the graphical sector, but also other sectors.
The name of the company is novexa and automates jobs with people that are on the autism spectrum.
The whole matchmaking and feedback process and so doesn't have to be in this prototype, we just want the general information pages and to convey a great look and brand identity that we will keep in the other pages to be developed. The website must be made with Wordpress, since the backend will be developed in Wordpress too.
It is a social project that wants to create possibilites for people with ASS to work from home for an employer or to do a variety of tasks for different customers.
The people we hire are generally not on the regular job market or have difficulty finding a job and "selling themselves"

Target Market(s)

matchmaking between talent (with ASS) and employers / jobs

Number of Pages Required

5+ page

Font styles to use
Sans Serif

Colors
ec1f27
e34298
a64599
6b449b
0355a3
0792cd

Requirements
Must have
• A stunning landing pages
• Integrate our logo and must match with what will do. We want a clean, modern, minimalistic, sleek website that radiates creativity and good looks.
• We have one page describing what we can do for customers, one page for people with ASS that would like to be candidates (our approach, learning program, ...), two pages that are addressed to partners who want to cooperate: the one's that can assist with autism related assistance and the one's that can help with the job coaching.
Nice to have
• In our logo are many colors as we embrace diversity and want to show that. Out main branding colors are red (for action) and blue for stability and will all gradients that go with it. Mainly white or black (or anthracite) for other parts
Should not have
• We want a modern and minimalistic design, no fluffy designs with lots of ornaments.

```html
<!DOCTYPE html>
<html lang="en">
<head>
<meta charset="utf-8">
<title>Novexa – Employment for people with autism</title>
<link href="https://fonts.googleapis.com/css2?family=Lato:wght@400;700;900&display=swap" rel="stylesheet">
<style>
:root{
  --red:#ec1f27;
  --pink:#e34298;
  --violet:#a64599;
  --purple:#6b449b;
  --blue:#0355a3;
  --sky:#0792cd;
  --navy:#0c3f8c;
  --card-blue:#1b74b8;
  --ink:#333333;
  --white:#ffffff;
}
*{margin:0;padding:0;box-sizing:border-box}
html,body{width:1200px;height:2535px;overflow:hidden}
body{position:relative;font-family:"Lato",sans-serif;color:var(--ink);background:var(--white)}
.abs{position:absolute}

/* Header */
.site-header{left:0;top:0;width:1200px;height:105px;background:var(--white)}
.brand{left:74px;top:30px;display:flex;align-items:center;gap:12px;font-weight:900;font-size:32px;letter-spacing:2px;color:var(--navy)}
.brand-mark{width:22px;height:22px;background:var(--navy)}
.menu-toggle{left:1092px;top:38px;width:34px;height:28px;display:flex;flex-direction:column;justify-content:space-between}
.menu-toggle span{display:block;height:6px;background:var(--navy);border-radius:1px}

/* Hero */
.hero{left:0;top:105px;width:1200px;height:575px;
  background:radial-gradient(ellipse 55% 60% at 50% 45%,#2d4fe0 0%,#1a2fb0 35%,#0c1460 65%,#070a22 100%)}
.hero-title{left:0;top:268px;width:1200px;text-align:center;font-weight:900;font-size:82px;letter-spacing:2px;color:var(--white);line-height:1}
.hero-sub{left:0;top:368px;width:1200px;text-align:center;font-weight:700;font-size:26px;line-height:35px;color:var(--white)}
.btn-play{left:497px;top:470px;width:206px;height:49px;background:var(--red);color:var(--white);border-radius:3px;
  display:flex;align-items:center;justify-content:center;gap:10px;font-weight:700;font-size:20px}

/* Welcome */
.photo{border:none}
.welcome-photo{left:74px;top:810px;width:512px;height:373px;
  background:linear-gradient(135deg,#3d5a2a 0%,#5d7d3c 35%,#a8a0a8 65%,#e6e0dc 100%)}
.section-heading{font-weight:900;font-size:54px;line-height:50px;color:var(--navy)}
.welcome-heading{left:676px;top:836px}
.body-copy{font-size:15.5px;line-height:27.6px;color:var(--ink);width:450px}
.welcome-copy{left:676px;top:958px}
.text-link{font-weight:700;font-size:15px;color:var(--pink);letter-spacing:.3px}
.welcome-link{left:676px;top:1137px}

/* What we do */
.services{left:0;top:1256px;width:1200px;height:461px;background:linear-gradient(90deg,var(--sky) 0%,#3a5a98 40%,#9b3868 70%,var(--red) 100%)}
.services-title{left:0;top:1297px;width:1200px;text-align:center;font-weight:900;font-size:54px;color:var(--white)}
.card-frame{width:223px;height:165px;border:13px solid var(--white);border-right:none;border-bottom:none}
.card{width:303px;height:235px;background:var(--white);text-align:center}
.card svg{position:absolute;left:116px;top:20px}
.card-title{position:absolute;left:0;top:108px;width:100%;font-weight:700;font-size:22px;color:var(--card-blue)}
.card-text{position:absolute;left:20px;top:144px;width:263px;font-size:14.5px;line-height:22.6px;color:var(--ink)}

/* Why choose */
.why-heading{left:74px;top:1901px}
.why-copy{left:74px;top:2028px}
.why-link{left:74px;top:2200px}
.why-photo{left:613px;top:1872px;width:513px;height:374px;
  background:linear-gradient(180deg,#b8d8ee 0%,#7fa84c 40%,#5f9a36 70%,#4a7f2a 100%)}

/* Footer */
.site-footer{left:0;top:2325px;width:1200px;height:210px;background:linear-gradient(90deg,var(--red) 0%,#b52050 45%,var(--purple) 100%);color:var(--white)}
.footer-col{top:2360px;width:260px;text-align:center}
.footer-col h3{font-weight:700;font-size:20px;margin-bottom:8px}
.footer-col p{font-size:13.5px;line-height:22px}
.footer-rule{left:0;top:2471px;width:1200px;height:1px;background:rgba(255,255,255,.35)}
.copyright{left:76px;top:2492px;font-size:12px;color:var(--white)}
.social{left:950px;top:2488px;display:flex;gap:16px}
.social span{width:22px;height:22px;border:2px solid var(--white);border-radius:50%}
</style>
</head>
<body>

<header class="site-header abs">
  <div class="brand abs"><span class="brand-mark"></span>NOVEXA</div>
  <div class="menu-toggle abs" aria-label="Menu"><span></span><span></span><span></span></div>
</header>

<section class="hero abs" role="img" aria-label="Abstract blue smoke on a dark background"></section>
<h1 class="hero-title abs">NOVEXA</h1>
<p class="hero-sub abs">Pellentesque habitant morbi tristique senectus<br>et netus et malesuada..</p>
<a class="btn-play abs">
  <svg width="26" height="26" viewBox="0 0 26 26"><circle cx="13" cy="13" r="12" fill="#fff"/><path d="M10 7.5 L19 13 L10 18.5 Z" fill="#ec1f27"/></svg>
  PLAY VIDEO
</a>

<div class="photo welcome-photo abs" role="img" aria-label="Young man smiling while drawing at a desk outdoors"></div>
<h2 class="section-heading welcome-heading abs">Welcome<br>to Novexa</h2>
<p class="body-copy welcome-copy abs">Lorem ipsum dolor sit amet, consectetur adipiscing elit. Maecenas tristique a erat efficitur feugiat. Etiam tincidunt rutrum ex nec vestibulum. Pellentesque habitant morbi tristique senectus et netus et malesuada fames ac turpis egestas tellus vestibulum quis rhoncus dui, non porttitor urna..</p>
<a class="text-link welcome-link abs">LEARN MORE ABOUT US &gt;&gt;</a>

<section class="services abs"></section>
<h2 class="services-title abs">What We Do</h2>

<div class="card-frame abs" style="left:74px;top:1401px"></div>
<div class="card abs" style="left:103px;top:1435px">
  <svg width="72" height="80" viewBox="0 0 72 80"><path d="M36 3 L69 21 L69 59 L36 77 L3 59 L3 21 Z" fill="none" stroke="#6b449b" stroke-width="2.5"/><circle cx="36" cy="32" r="8" fill="#ec1f27"/><path d="M22 56 Q22 42 36 42 Q50 42 50 56 Z" fill="#ec1f27"/></svg>
  <div class="card-title">Vivamus Massa</div>
  <p class="card-text">Pellentesque habitant morbi tristique senectus et netus et malesuada malesuada tortor..</p>
</div>

<div class="card-frame abs" style="left:434px;top:1401px"></div>
<div class="card abs" style="left:463px;top:1435px">
  <svg width="72" height="80" viewBox="0 0 72 80"><path d="M36 3 L69 21 L69 59 L36 77 L3 59 L3 21 Z" fill="none" stroke="#6b449b" stroke-width="2.5"/><rect x="29" y="27" width="14" height="8" rx="2" fill="none" stroke="#ec1f27" stroke-width="3"/><rect x="20" y="33" width="32" height="22" rx="3" fill="#ec1f27"/><rect x="26" y="33" width="2" height="22" fill="#fff"/><rect x="44" y="33" width="2" height="22" fill="#fff"/></svg>
  <div class="card-title">Vivamus Massa</div>
  <p class="card-text">Pellentesque habitant morbi tristique senectus et netus et malesuada malesuada tortor..</p>
</div>

<div class="card-frame abs" style="left:794px;top:1401px"></div>
<div class="card abs" style="left:823px;top:1435px">
  <svg width="72" height="80" viewBox="0 0 72 80"><path d="M36 3 L69 21 L69 59 L36 77 L3 59 L3 21 Z" fill="none" stroke="#6b449b" stroke-width="2.5"/><circle cx="33" cy="37" r="10" fill="none" stroke="#ec1f27" stroke-width="4"/><path d="M40 44 L50 54" stroke="#ec1f27" stroke-width="5" stroke-linecap="round"/></svg>
  <div class="card-title">Vivamus Massa</div>
  <p class="card-text">Pellentesque habitant morbi tristique senectus et netus et malesuada malesuada tortor..</p>
</div>

<h2 class="section-heading why-heading abs">Why Choose<br>Novexa</h2>
<p class="body-copy why-copy abs">Lorem ipsum dolor sit amet, consectetur adipiscing elit. Maecenas tristique a erat efficitur feugiat. Etiam tincidunt rutrum ex nec vestibulum. Pellentesque habitant morbi tristique senectus et netus et malesuada fames ac turpis egestas tellus vestibulum quis rhoncus dui, non porttitor urna..</p>
<a class="text-link why-link abs">MORE ABOUT PROJECTS &gt;&gt;</a>
<div class="photo why-photo abs" role="img" aria-label="Man driving a red ride-on lawn mower across a green field"></div>

<footer class="site-footer abs"></footer>
<div class="footer-col abs" style="left:200px">
  <h3>Address Info</h3>
  <p>14 Harbor Lane, Suite 5<br>Westfield City</p>
</div>
<div class="footer-col abs" style="left:470px">
  <h3>Contact Us</h3>
  <p>1-800-555-0142 &nbsp;I&nbsp; 100-555-0187</p>
</div>
<div class="footer-col abs" style="left:740px">
  <h3>Email Us</h3>
  <p>hello@novexa-mail.net</p>
</div>
<div class="footer-rule abs"></div>
<p class="copyright abs">Copyright © 2019 Novexa All rights reserved. Terms and Condition</p>
<div class="social abs" aria-label="Social links"><span></span><span></span><span></span><span></span><span></span></div>

</body>
</html>
```